professional business card design for technology company

We are a small technology consulting firm, specialising in consulting based around Cloud and Managed services. Our colour scheme is yellow, blue and white, as you can see in the logos. Although we are based in melbourne australia, due to the nature of our work, our clients can be located anywhere. We are looking for a clean, professional, positive look - similar to our company logo

Target Market(s)

small business

Industry/Entity Type

Business

Contact Information for Business Card

eye catching, designed to incorporate some level of raised printing. Must contain website address, phone number, name and job title

Requirements
Must have
• Logo (attached) - use of the same colour scheme

```html
<!DOCTYPE html>
<html lang="en">
<head>
<meta charset="utf-8">
<title>Nimbara Business Card</title>
<link href="https://fonts.googleapis.com/css2?family=Raleway:wght@400;500;600;800&display=swap" rel="stylesheet">
<style>
  :root {
    --stage: #e6e3df;
    --card: #161616;
    --panel: #0d0d0d;
    --yellow: #f5d200;
    --blue: #29a3dd;
    --white: #f4f4f4;
    --grey: #8a8a8a;
    --text-light: #d8d8d8;
  }
  * { margin: 0; padding: 0; box-sizing: border-box; }
  html, body {
    width: 1200px; height: 960px; overflow: hidden;
    background: var(--stage);
    font-family: "Raleway", sans-serif;
  }
  .canvas { position: relative; width: 1200px; height: 960px; }
  .card {
    position: absolute; left: 250px; width: 700px; height: 400px;
    background: var(--card);
    box-shadow: 0 6px 18px rgba(0,0,0,0.25);
    overflow: hidden;
  }
  .card--back { top: 50px; }
  .card--front { top: 510px; }

  .brand-frame {
    position: absolute;
    border: 5px solid var(--yellow);
  }
  .brand-panel {
    position: absolute; inset: 6px;
    background: var(--panel);
    display: flex; align-items: center; justify-content: center; gap: 22px;
  }
  .brand-dot {
    width: 46px; height: 46px; border-radius: 50%;
    background: var(--blue);
  }
  .brand-name {
    font-weight: 800; color: var(--white);
    font-size: 88px; letter-spacing: -2px; line-height: 1;
  }

  .card--back .brand-frame { left: 80px; top: 70px; width: 540px; height: 190px; }
  .card--front .brand-frame { left: 150px; top: 30px; width: 520px; height: 180px; }
  .card--front .brand-name { font-size: 80px; }

  .contact-line {
    display: flex; align-items: center; gap: 14px;
    color: var(--text-light); font-size: 17px; letter-spacing: 0.5px;
  }
  .card--back .contact-line {
    position: absolute; left: 0; right: 0; top: 310px;
    justify-content: center; letter-spacing: 2px;
  }
  .icon-ring {
    width: 32px; height: 32px; border-radius: 50%;
    border: 2px solid var(--blue);
    display: flex; align-items: center; justify-content: center;
  }
  .icon-ring svg { width: 16px; height: 16px; }

  .holder {
    position: absolute; left: 50px; top: 235px;
    display: flex; align-items: center; gap: 14px;
  }
  .holder .icon-ring { width: 40px; height: 40px; }
  .holder .icon-ring svg { width: 20px; height: 20px; }
  .holder-name { font-size: 21px; font-weight: 600; letter-spacing: 0.5px; }
  .holder-first { color: var(--grey); }
  .holder-last { color: var(--blue); font-weight: 500; }
  .holder-role { font-size: 14px; color: var(--grey); margin-top: 1px; }

  .contact-list {
    position: absolute; left: 440px; top: 258px;
    display: flex; flex-direction: column; gap: 14px;
  }
</style>
</head>
<body>
<div class="canvas">

  <section class="card card--back" aria-label="Card back">
    <div class="brand-frame">
      <div class="brand-panel">
        <span class="brand-dot"></span>
        <span class="brand-name">Nimbara</span>
      </div>
    </div>
    <div class="contact-line">
      <svg width="14" height="14" viewBox="0 0 16 16" aria-hidden="true">
        <circle cx="8" cy="8" r="7" fill="var(--blue)"/>
        <path d="M1 8h14M8 1c-3 3-3 11 0 14M8 1c3 3 3 11 0 14" stroke="#111" stroke-width="1.2" fill="none"/>
      </svg>
      <span>www.nimbara.com</span>
    </div>
  </section>

  <section class="card card--front" aria-label="Card front">
    <div class="brand-frame">
      <div class="brand-panel">
        <span class="brand-dot"></span>
        <span class="brand-name">Nimbara</span>
      </div>
    </div>

    <div class="holder">
      <span class="icon-ring">
        <svg viewBox="0 0 16 16" aria-hidden="true">
          <circle cx="8" cy="5" r="3.2" fill="var(--white)"/>
          <path d="M2 15c0-4 3-6 6-6s6 2 6 6z" fill="var(--white)"/>
        </svg>
      </span>
      <div>
        <div class="holder-name"><span class="holder-first">DANIEL</span> <span class="holder-last">HART</span></div>
        <div class="holder-role">Sales Director</div>
      </div>
    </div>

    <div class="contact-list">
      <div class="contact-line">
        <span class="icon-ring">
          <svg viewBox="0 0 16 16" aria-hidden="true">
            <rect x="1" y="3" width="14" height="10" rx="1" fill="var(--white)"/>
            <path d="M1.5 3.5L8 9l6.5-5.5" stroke="#111" stroke-width="1.3" fill="none"/>
          </svg>
        </span>
        <span>hello@nimbara.com</span>
      </div>
      <div class="contact-line">
        <span class="icon-ring">
          <svg viewBox="0 0 16 16" aria-hidden="true">
            <circle cx="8" cy="8" r="7" fill="var(--white)"/>
            <path d="M1 8h14M8 1c-3 3-3 11 0 14M8 1c3 3 3 11 0 14" stroke="#111" stroke-width="1.2" fill="none"/>
          </svg>
        </span>
        <span>www.nimbara.com</span>
      </div>
      <div class="contact-line">
        <span class="icon-ring">
          <svg viewBox="0 0 16 16" aria-hidden="true">
            <path d="M4 1.5l2.5 3-1.5 2c1 2 2.5 3.5 4.5 4.5l2-1.5 3 2.5-1.5 2.5C7 14 2 9 1.5 3z" fill="var(--white)"/>
          </svg>
        </span>
        <span>555-018-2047</span>
      </div>
    </div>
  </section>

</div>
</body>
</html>
```